Kelvor Engineers: Why you should hire us keepsake

New design. Open to plastic cards. We are an engineering firm that designs cell phone towers and commercial buildings. Please check out our website www.kelvorstruct.com for more details. We want people to remember our card and for it to be useful if possible. We want the same look and feel on these cards to be translated to other marketing material we may need such as brochures.

Target Market(s)

Architects, Developers and Telecommunication Carriers

Industry/Entity Type

Engineering

Contact Information for Business Card

Card with our company colors, logo, and innovative design with elements related to our industry.

Font styles to use
Sans Serif

Colors
9bcb3c
abd036
0255a3

Requirements
Must have
• Sleek and hip design
Nice to have
• Bright lime green and navy coloring that pops with an innovative design.
Should not have
• A basic and boring design

```html
<!DOCTYPE html>
<html lang="en">
<head>
<meta charset="utf-8">
<title>Kelvor Engineers – Business Card</title>
<link rel="stylesheet" href="https://fonts.googleapis.com/css2?family=Roboto:wght@400;500;900&family=Roboto+Condensed:wght@700&display=swap">
<style>
  :root {
    --backdrop: #8b8682;
    --card-dark: #1b1c1e;
    --card-light: #f1f1f1;
    --lime: #00ff00;
    --navy: #002d5f;
    --white: #ffffff;
    --tagline: #e6ffe0;
    --icon: #0b2a4a;
  }
  * { margin: 0; padding: 0; box-sizing: border-box; }
  html, body { width: 1200px; height: 960px; overflow: hidden; }
  body {
    background: var(--backdrop);
    position: relative;
    font-family: "Roboto", Arial, sans-serif;
  }
  .card {
    position: absolute;
    left: 320px;
    width: 600px;
    border-radius: 22px;
    overflow: hidden;
    box-shadow: 0 4px 10px rgba(0,0,0,0.35);
  }
  .card--front { top: 105px; height: 350px; background: var(--card-dark); }
  .card--back  { top: 493px; height: 342px; background: var(--card-light); }

  .wordmark {
    position: absolute;
    left: 0; right: 0;
    text-align: center;
    font-family: "Roboto", Arial, sans-serif;
    font-weight: 900;
    font-size: 54px;
    letter-spacing: -1px;
    color: var(--lime);
    line-height: 1;
  }
  .card--front .wordmark { top: 140px; }
  .card--back .wordmark  { top: 95px; }

  .tagline {
    position: absolute;
    top: 270px; left: 0; right: 0;
    display: flex; justify-content: center; align-items: center; gap: 4px;
    font-family: "Roboto Condensed", Arial, sans-serif;
    font-weight: 700;
    font-size: 15px;
    color: var(--tagline);
  }
  .tagline::before, .tagline::after {
    content: ""; width: 28px; height: 1.5px; background: var(--tagline);
  }
  .locations {
    position: absolute;
    top: 291px; left: 0; right: 0;
    text-align: center;
    font-size: 15px;
    letter-spacing: 0.3px;
    color: var(--white);
  }

  .contact-band {
    position: absolute;
    left: 0; right: 0; bottom: 0;
    height: 98px;
    display: flex;
  }
  .contact-band__name {
    width: 300px;
    background: var(--navy);
    display: flex; align-items: center; justify-content: center;
    padding-left: 24px;
    font-family: "Roboto Condensed", Arial, sans-serif;
    font-weight: 700;
    font-size: 20px;
    color: var(--lime);
    text-transform: uppercase;
  }
  .contact-band__details {
    flex: 1;
    margin-left: 3px;
    background: var(--lime);
    padding: 9px 0 0 37px;
    list-style: none;
  }
  .contact-band__details li {
    display: flex; align-items: center; gap: 8px;
    height: 19px;
    font-size: 14px;
    color: var(--white);
  }
  .contact-band__details svg { width: 13px; height: 13px; fill: var(--icon); flex: none; }
</style>
</head>
<body>

<section class="card card--front">
  <div class="wordmark">Kelvor Engineers</div>
  <div class="tagline">MULTI-DISCIPLINE ENGINEERING</div>
  <div class="locations">Atlanta | Charlotte | Houston | San Antonio</div>
</section>

<section class="card card--back">
  <div class="wordmark">Kelvor Engineers</div>
  <div class="contact-band">
    <div class="contact-band__name">Dana Holloway Pierce</div>
    <ul class="contact-band__details">
      <li>
        <svg viewBox="0 0 16 16" aria-hidden="true"><path d="M3.5 1l2.5 3-1.5 2a9 9 0 0 0 5 5l2-1.5 3 2.5-1.5 2.5C8 15 1 8 1 2.5z"/></svg>
        555.214.7730
      </li>
      <li>
        <svg viewBox="0 0 16 16" aria-hidden="true"><path d="M4 0h8v16H4zM5.5 2v10h5V2zM7 13.5h2v1H7z" fill-rule="evenodd"/></svg>
        555.368.4192
      </li>
      <li>
        <svg viewBox="0 0 16 16" aria-hidden="true"><path d="M1 3h14v2L8 9 1 5zM1 6.5l7 4 7-4V13H1z"/></svg>
        dpierce@kelvorstruct.com
      </li>
      <li>
        <svg viewBox="0 0 16 16" aria-hidden="true"><circle cx="8" cy="8" r="7"/><path d="M1 8h14M8 1c3 3 3 11 0 14M8 1c-3 3-3 11 0 14" stroke="#00ff00" stroke-width="1" fill="none"/></svg>
        www.kelvorstruct.com
      </li>
    </ul>
  </div>
</section>

</body>
</html>
```